BOLD & MINIMALIST DESIGN NEEDED

We want a very bold but minimalistic business card design that is impactful and utilizes both sides of the business card. Our current logo is included for your use.

We want bold fonts and good use of negative space. We don't want the logo to overpower the design.

Target Market(s)

Professionals who are building new commercial buildings.

Industry/Entity Type

Construction

Contact Information for Business Card

Name, Title, email, office phone, cell phone, website

Font styles to use
Serif
Sans Serif

Requirements
Must have
• Bold design!

```html
<!DOCTYPE html>
<html lang="en">
<head>
<meta charset="utf-8">
<title>Crestline — Business Card</title>
<link rel="stylesheet" href="https://fonts.googleapis.com/css2?family=Poppins:wght@400;500;700&display=swap">
<style>
  :root {
    --ink: #0b0c0e;
    --paper: #ffffff;
    --lime: #86c226;
    --stage: #c4c4c4;
    --soft-white: #f2f2f2;
  }
  * { box-sizing: border-box; margin: 0; padding: 0; }
  html, body { width: 1200px; height: 1015px; overflow: hidden; }
  body {
    background: var(--stage);
    font-family: "Poppins", Arial, sans-serif;
    position: relative;
  }
  .card {
    position: absolute;
    left: 250px;
    width: 700px;
    height: 400px;
    overflow: hidden;
    box-shadow: 0 10px 24px rgba(0,0,0,0.28);
  }
  .card-front { top: 70px; background: var(--ink); }
  .card-back  { top: 540px; background: var(--paper); }

  /* Front */
  .front-band {
    position: absolute; left: 0; right: 0; bottom: 0;
    height: 18px; background: var(--lime);
  }
  .brand {
    position: absolute; inset: 0 0 18px 0;
    display: flex; align-items: center; justify-content: center;
    gap: 18px;
  }
  .brand-square { width: 38px; height: 38px; background: var(--lime); }
  .brand-name {
    color: var(--soft-white); font-weight: 700; line-height: 1;
    font-size: 60px; letter-spacing: 1px;
  }

  /* Back */
  .back-shapes { position: absolute; inset: 0; }
  .person { position: absolute; left: 48px; top: 120px; }
  .person-name { font-size: 30px; font-weight: 700; color: var(--ink); line-height: 1.1; }
  .person-title { font-size: 22px; font-weight: 500; color: var(--lime); line-height: 1.2; }
  .back-brand {
    position: absolute; right: 36px; top: 56px;
    font-size: 26px; font-weight: 700; color: var(--paper); letter-spacing: 1px;
  }
  .contact-list {
    position: absolute; left: 48px; bottom: 26px;
    list-style: none; color: var(--paper);
    font-size: 19px; font-weight: 400; line-height: 1.4;
  }
  .contact-list li { display: flex; align-items: center; gap: 12px; }
  .contact-list svg { width: 18px; height: 18px; flex: none; }
  .website {
    position: absolute; right: 36px; bottom: 120px;
    color: var(--paper); font-size: 18px;
  }
  .website .accent { color: var(--lime); }
</style>
</head>
<body>

<section class="card card-front" aria-label="Card front">
  <div class="brand">
    <span class="brand-square" aria-hidden="true"></span>
    <span class="brand-name">CRESTLINE</span>
  </div>
  <div class="front-band"></div>
</section>

<section class="card card-back" aria-label="Card back">
  <svg class="back-shapes" width="700" height="400" viewBox="0 0 700 400" aria-hidden="true">
    <polygon points="0,400 0,282 420,282 520,0 700,0 700,400" fill="var(--ink)"/>
    <polygon points="0,248 432,248 420,282 0,282" fill="var(--lime)"/>
  </svg>

  <div class="person">
    <p class="person-name">MARCUS HALE</p>
    <p class="person-title">Managing Director</p>
  </div>

  <p class="back-brand">CRESTLINE</p>

  <p class="website">www.<span class="accent">crestlinebuild</span>.com</p>

  <ul class="contact-list">
    <li>
      <svg viewBox="0 0 24 24" aria-hidden="true"><path fill="var(--lime)" d="M6.6 10.8a15.1 15.1 0 0 0 6.6 6.6l2.2-2.2a1 1 0 0 1 1-.25 11.4 11.4 0 0 0 3.6.57 1 1 0 0 1 1 1V20a1 1 0 0 1-1 1A17 17 0 0 1 3 4a1 1 0 0 1 1-1h3.5a1 1 0 0 1 1 1c0 1.25.2 2.45.57 3.57a1 1 0 0 1-.25 1z"/></svg>
      044-987 654 321
    </li>
    <li>
      <svg viewBox="0 0 24 24" aria-hidden="true"><rect x="6" y="2" width="12" height="20" rx="2" fill="none" stroke="var(--lime)" stroke-width="2"/><circle cx="12" cy="18" r="1.2" fill="var(--lime)"/></svg>
      044-987 654 321
    </li>
    <li>
      <svg viewBox="0 0 24 24" aria-hidden="true"><rect x="2" y="5" width="20" height="14" fill="var(--lime)"/><path d="M2 5l10 8 10-8" fill="none" stroke="var(--ink)" stroke-width="1.6"/></svg>
      info@crestlinebuild.com
    </li>
  </ul>
</section>

</body>
</html>
```